Celvara Health Group Presentation Folder, for Cancer Awareness, VERY COLORFUL AND MODERN

Presentation Folder I know pretty much what i want so it should be very eazy , I have included files from folders I use now rebrand them to my new company they will be fine, no sense re creating the wheel
Full Bleed Size
20.87" x 16.68"
53 x 42.4 cm
6260 x 5004 pixels
Document Trim Size
20.75" x 16.56"
52.7 x 42.1 cm
6225 x 4969 pixels

Low design quality

Industry/Entity Type

Medical

Font styles to use
Serif

Colors

Designer to choose colors to be used in the design.

Requirements
Must have
• really I am not looking for some one to redesign, we like our folder front page and would like to see new word information added., there are two folder front pages to choose from
• So Keep the original front page and redesign the back page and the pockets
• Can Make your Design off of one of the ones I already uploaded
Nice to have
• Keep the same color schemes, Keep the original front page and redesign the back page and the pockets
Should not have
• DO not recreate the front covers, use what I gave you and just rebrand

```html
<!DOCTYPE html>
<html lang="en">
<head>
<meta charset="utf-8">
<title>Celvara Health Group – Presentation Folder</title>
<link rel="stylesheet" href="https://fonts.googleapis.com/css2?family=Cinzel:wght@400;600&family=Raleway:wght@400;700;800&family=Comic+Neue:wght@700&display=swap">
<style>
  :root {
    --navy: #1b2152;
    --green: #8dc63f;
    --green-light: #b5dd85;
    --white: #ffffff;
    --dieline: #e0262b;
    --fold: #3cb878;
    --ink: #1b2152;
    --photo-grey-a: #e9e9e9;
    --photo-grey-b: #9a9a9a;
    --photo-teal-a: #d9ebee;
    --photo-teal-b: #4f8a95;
  }
  html, body { margin: 0; padding: 0; overflow: hidden; background: var(--white); }
  .canvas { width: 1200px; height: 1200px; display: block; }
  .title-serif { font-family: "Cinzel", serif; }
  .body-sans { font-family: "Raleway", sans-serif; }
  .tagline-hand { font-family: "Comic Neue", cursive; }
</style>
</head>
<body>
<svg class="canvas" viewBox="0 0 1500 1500" xmlns="http://www.w3.org/2000/svg">
  <defs>
    <linearGradient id="title-band" x1="0" x2="1">
      <stop offset="0" stop-color="var(--green)"/>
      <stop offset="1" stop-color="var(--green-light)"/>
    </linearGradient>
    <linearGradient id="beach-photo" x1="0" y1="0" x2="0" y2="1">
      <stop offset="0" stop-color="var(--photo-grey-b)"/>
      <stop offset="0.5" stop-color="var(--photo-grey-a)"/>
      <stop offset="1" stop-color="#c8c8c8"/>
    </linearGradient>
    <linearGradient id="dinner-photo" x1="0" y1="0" x2="1" y2="1">
      <stop offset="0" stop-color="var(--photo-teal-a)"/>
      <stop offset="1" stop-color="var(--photo-teal-b)"/>
    </linearGradient>
    <linearGradient id="ribbon-fill" x1="0" y1="0" x2="1" y2="1">
      <stop offset="0" stop-color="#c77bb8"/>
      <stop offset="1" stop-color="#4fb4e3"/>
    </linearGradient>
    <clipPath id="pocket-left-clip">
      <path d="M136,945 L748,945 L710,1212 Q705,1237 680,1237 L136,1237 Z"/>
    </clipPath>
    <clipPath id="pocket-right-clip">
      <path d="M758,945 L1372,945 L1372,1237 L828,1237 Q803,1237 799,1212 Z"/>
    </clipPath>
  </defs>

  <!-- Outer cover spread -->
  <g class="cover-spread">
    <rect class="cover-paper" x="132" y="165" width="1243" height="780" fill="var(--white)"/>

    <!-- Back cover (left) -->
    <g class="back-cover">
      <rect class="header-band" x="132" y="200" width="621" height="58" fill="var(--green)"/>
      <rect class="family-photo" x="175" y="307" width="543" height="328" fill="url(#beach-photo)" role="img" aria-label="Black and white photo of a multi-generation family walking hand in hand on a beach"/>
      <text class="body-sans intro-copy" font-size="9.6" fill="var(--ink)" text-anchor="middle">
        <tspan x="446" y="657"><tspan font-weight="800">Hereditary cancer screening</tspan> provides vital information to help people with a strong personal or family history of</tspan>
        <tspan x="446" y="669">cancer understand their own risk of developing the disease. With this information, they can take steps to Potentially</tspan>
        <tspan x="446" y="681">Prevent Cancer, Delay the Onset of Cancer or Catch it at an Earlier stage when outcomes and survival rates are Better.</tspan>
      </text>
      <text class="body-sans motto" font-size="12.5" font-weight="800" fill="var(--ink)" text-anchor="middle">
        <tspan x="446" y="711">Don’t be Afraid of the Answer: Knowledge is Power and Power Eradicates Fear.</tspan>
        <tspan x="446" y="727">When You are Fearless, You Will Make all the Right Choices!</tspan>
      </text>
      <g class="brand-lockup">
        <circle cx="397" cy="780" r="26" fill="var(--navy)"/>
        <text class="title-serif" font-size="19" font-weight="600" fill="var(--navy)">
          <tspan x="434" y="769">CELVARA</tspan>
          <tspan x="434" y="788">HEALTH</tspan>
          <tspan x="434" y="807">GROUP</tspan>
        </text>
      </g>
    </g>

    <!-- Front cover (right) -->
    <g class="front-cover">
      <rect class="title-band" x="753" y="200" width="622" height="58" fill="url(#title-band)"/>
      <text class="title-serif cover-title" x="1064" y="239" font-size="27" fill="var(--white)" text-anchor="middle" letter-spacing="1">HEREDITARY CANCER SCREENING</text>
      <rect class="subtitle-box" x="797" y="259" width="535" height="47" fill="var(--navy)"/>
      <text class="title-serif subtitle" x="1064" y="288" font-size="14" fill="var(--white)" text-anchor="middle" letter-spacing="0.5">DOCTORS ARE THE GATEKEEPERS TO GENETIC TESTING</text>
      <rect class="awareness-ribbon" x="786" y="278" width="58" height="88" rx="6" fill="url(#ribbon-fill)" role="img" aria-label="Pink and blue cancer awareness ribbon"/>
      <text class="body-sans cover-lede" font-size="10" fill="var(--ink)" text-anchor="middle">
        <tspan x="1064" y="324">We have an obligation to help patients understand genetic risk and how</tspan>
        <tspan x="1064" y="336">testing can guide heath care decisions</tspan>
      </text>
      <rect class="dinner-photo" x="753" y="360" width="622" height="470" fill="url(#dinner-photo)" role="img" aria-label="Teal-toned photo of a family sharing a meal around an outdoor table"/>
    </g>

    <!-- Bottom band across spread -->
    <rect class="footer-band" x="132" y="835" width="1243" height="52" fill="var(--navy)"/>
    <circle class="footer-badge" cx="858" cy="883" r="38" fill="var(--white)"/>
    <text class="tagline-hand footer-tagline" x="908" y="865" font-size="15" font-weight="700" fill="var(--white)" letter-spacing="1">The Test You Order FOR Your Patients</text>
  </g>

  <!-- Pockets -->
  <g class="pocket pocket-left" clip-path="url(#pocket-left-clip)">
    <rect x="136" y="945" width="612" height="292" fill="var(--navy)"/>
    <rect class="pocket-pattern" x="136" y="945" width="210" height="252" fill="#262d66" role="img" aria-label="Decorative pattern of large white curved shapes"/>
    <rect class="pocket-strip" x="136" y="1197" width="612" height="40" fill="var(--green)"/>
  </g>
  <g class="pocket pocket-right" clip-path="url(#pocket-right-clip)">
    <rect x="758" y="945" width="614" height="292" fill="var(--navy)"/>
    <rect class="pocket-strip" x="758" y="1197" width="614" height="40" fill="var(--green)"/>
  </g>
  <g class="pocket-imprint" transform="rotate(180 1235 975)">
    <text class="title-serif" x="1235" y="966" font-size="15" fill="var(--white)" text-anchor="middle">CELVARA HEALTH GROUP</text>
    <text class="body-sans" x="1235" y="980" font-size="9" fill="var(--green)" text-anchor="middle">a division of Northlane Medical Sales LLC</text>
  </g>

  <!-- Business card slits -->
  <g class="card-slits" stroke="var(--dieline)" stroke-width="1">
    <line x1="325" y1="1062" x2="365" y2="1022"/>
    <line x1="518" y1="1022" x2="558" y2="1062"/>
    <line x1="325" y1="1120" x2="365" y2="1160"/>
    <line x1="518" y1="1160" x2="558" y2="1120"/>
  </g>

  <!-- Dieline -->
  <g class="dieline" fill="none" stroke="var(--dieline)" stroke-width="1">
    <path d="M132,165 L1375,165"/>
    <path d="M132,165 L83,170 L83,630 A25,25 0 0 1 83,680 L83,932 L132,945"/>
    <path d="M1375,165 L1424,170 L1424,630 A25,25 0 0 0 1424,680 L1424,932 L1375,945"/>
    <path d="M136,945 L136,1237 L680,1237 Q705,1237 710,1212 L748,945"/>
    <path d="M758,945 L799,1212 Q803,1237 828,1237 L1372,1237 L1372,945"/>
  </g>

  <!-- Fold lines -->
  <g class="fold-lines" stroke="var(--fold)" stroke-width="1" stroke-dasharray="3 3" fill="none">
    <line x1="132" y1="165" x2="132" y2="945"/>
    <line x1="753" y1="165" x2="753" y2="945"/>
    <line x1="1375" y1="165" x2="1375" y2="945"/>
    <line x1="132" y1="945" x2="1375" y2="945"/>
  </g>
</svg>
</body>
</html>
```